Website Redesign - We Need Your Magic!

Hello we are looking for you to help us re-design a high end and professional website for a high-end private school.

Here is the current site: http://www.ferndalecrest.com/

NOTE THIS IS DESIGN ONLY, NO CODING :)

The image they want to portray is that of high quality sports and education, in a creative "un-stiff" way.

Menu Bar: Horizontal

Look and Feel:

Site Colors: Dark green and a Gold yellow (logos are attached)

This site will represent a school so the look must be clean, bold, and classy. The site must have a very clean user interface, with things easily recognizable. Think simple.

The site should be visually appealing! If you come to me with templates, or a ton of text you will be out.

This site should be outside the box, we do not want boring, we do not want status quo. This site should instill excitement, innovation, and athletics.

So the main points again are:

1. High-end and classy look, with creative feel
2. Simple and clear navigation style
3. To cover the Junior and High School - Ferndale Crest College Schools

Think outside the box. We look forward to seeing what you come up with!!

Thank you for helping us create an amazing site for the school!

Industry/Entity Type

School

```html
<!DOCTYPE html>
<html lang="en">
<head>
<meta charset="utf-8">
<title>Ferndale Crest College</title>
<link href="https://fonts.googleapis.com/css2?family=Oswald:wght@400;500&family=Open+Sans:wght@400;600;700&display=swap" rel="stylesheet">
<style>
:root{
  --green:#0b5a2a;
  --green-dark:#08481f;
  --green-deep:#063b19;
  --gold:#f5e11a;
  --ink:#333;
  --ink-soft:#555;
  --rule:#e2e2e2;
  --band:#e3e3e3;
  --white:#fff;
  --pale:#cfe0cf;
}
*{box-sizing:border-box;margin:0;padding:0}
html,body{width:1200px;height:2769px;overflow:hidden;background:var(--white)}
body{font-family:"Open Sans",Arial,sans-serif;color:var(--ink);position:relative}
.wrap{position:absolute;left:162px;width:876px}
h2.section-title{font-family:"Oswald",Arial,sans-serif;font-weight:500;font-size:20px;text-transform:uppercase;color:#222;letter-spacing:.3px;white-space:nowrap}
h2.section-title span{color:var(--green)}
h2.section-title::after{content:"";display:block;width:56px;height:3px;background:var(--green);margin-top:8px}
p{font-size:12.5px;line-height:21px;color:var(--ink-soft)}

.site-header{position:absolute;top:0;left:0;width:1200px;height:138px;background:var(--green)}
.brand{position:absolute;left:166px;top:20px;display:flex;align-items:center;gap:10px;color:var(--gold);font-family:"Oswald",sans-serif;font-size:18px}
.brand .dot{width:22px;height:22px;border-radius:50%;background:var(--gold)}
.info{position:absolute;left:652px;top:24px;color:var(--white);display:flex;gap:8px;align-items:center}
.info .label{font-family:"Oswald",sans-serif;font-size:11.5px;letter-spacing:.3px}
.info .phone{font-family:"Oswald",sans-serif;font-size:24px;color:var(--gold);line-height:26px}
.search{position:absolute;left:866px;top:24px;color:var(--white);font-family:"Oswald",sans-serif;font-size:11.5px}
.search .box{margin-top:5px;width:174px;height:24px;background:var(--white);border-radius:2px;font-family:"Open Sans",sans-serif;font-size:10px;color:#888;padding:5px 8px;position:relative}
.search svg{position:absolute;right:6px;top:5px}
.nav{position:absolute;top:94px;left:355px;width:685px;display:flex;justify-content:space-between;font-family:"Oswald",sans-serif;font-size:13px;color:var(--white);text-transform:uppercase}
.nav .active{border-bottom:2px solid var(--white);padding-bottom:4px}

.mosaic{position:absolute;top:138px;left:0;width:1200px;height:480px;display:grid;grid-template-columns:230px 140px 105px 105px 140px 240px 240px;grid-template-rows:240px 240px}
.mosaic div{border:1px solid rgba(255,255,255,.35)}

.welcome{top:664px}
.welcome .text{width:500px;margin-top:22px}
.welcome .text p{font-size:12px;line-height:20px}
.welcome .text p+p{margin-top:16px}
.video{position:absolute;left:523px;top:0;width:353px;height:238px;background:linear-gradient(180deg,#7c8f6c,#4f6a3c 60%,#70793d)}
.video .play{position:absolute;left:152px;top:94px}
.rule{position:absolute;left:162px;width:876px;height:1px;background:var(--rule)}

.note{position:absolute;top:992px;width:420px}
.note .row{display:flex;gap:22px;margin-top:22px}
.note .photo{flex:0 0 150px;height:150px}
.note p{font-size:11.5px;line-height:19px}
.btn-more{display:inline-block;margin-top:12px;border:1px solid var(--green);color:var(--green);font-size:10.5px;padding:3px 9px;border-radius:3px}

.calendar{top:1350px}
.cal-table{position:absolute;top:60px;left:0;width:876px;border-collapse:collapse}
.cal-table th{font-family:"Oswald",sans-serif;font-weight:400;font-size:16px;color:var(--green);height:40px;text-transform:uppercase}
.cal-table td{height:55px;font-size:11.5px;text-align:center;line-height:17px;color:#333}
.cal-table td.label{text-align:left;padding-left:14px;font-family:"Oswald",sans-serif;font-size:14px;text-transform:uppercase;color:#222;width:180px}
.cal-table tr.band td{background:var(--band)}
.downloads{position:absolute;top:1766px;left:162px;width:876px;height:108px;background:var(--green);border-bottom:4px solid var(--green-deep);display:flex;gap:24px;padding-left:150px;align-items:center}
.btn-gold{width:276px;height:46px;background:var(--gold);font-family:"Oswald",sans-serif;font-size:14px;color:#1d3a10;display:flex;align-items:center;justify-content:center;text-transform:uppercase;border-bottom:3px solid #c9b40d}

.events{top:1910px}
.event{position:absolute;top:62px;width:203px}
.event .photo{height:132px}
.event .date{font-family:"Oswald",sans-serif;font-size:15px;color:#222;margin-top:24px;text-transform:uppercase}
.event .cap{font-size:11.5px;color:var(--ink-soft);margin-top:6px}
.sports{position:absolute;left:674px;top:0;width:202px}
.sports ul{list-style:none;margin-top:22px}
.sports li{font-size:11.5px;color:var(--ink-soft);height:36px;line-height:36px;border-bottom:1px solid var(--rule)}

.partners{position:absolute;top:2257px;left:188px;width:824px;display:flex;justify-content:space-between}
.partner{width:150px;height:88px;border:1px solid #ddd;display:flex;align-items:center;justify-content:center}
.partner span{width:100px;height:44px;border-radius:6px;background:#d9dde4}

.site-footer{position:absolute;top:2440px;left:0;width:1200px;height:290px;background:var(--green)}
.footer-title{font-family:"Oswald",sans-serif;font-weight:500;font-size:18px;color:var(--white);text-transform:uppercase;white-space:nowrap}
.footer-title span{color:var(--gold)}
.footer-title::after{content:"";display:block;width:50px;height:3px;background:var(--gold);margin-top:7px}
.touch{position:absolute;left:162px;top:40px;width:334px}
.touch .grid{display:grid;grid-template-columns:1fr 1fr;row-gap:24px;margin-top:26px;text-align:center}
.touch .item{color:var(--white);font-size:11px;line-height:16px}
.touch .item b{display:block;color:var(--gold);font-family:"Oswald",sans-serif;font-weight:400;font-size:12px;text-transform:uppercase}
.touch .ico{width:30px;height:30px;border-radius:50%;background:var(--gold);margin:0 auto 8px;display:flex;align-items:center;justify-content:center}
.feed{position:absolute;left:535px;top:40px;width:192px}
.feed-box{margin-top:26px;background:var(--white);height:122px;padding:6px;font-size:9.5px;color:#555}
.feed-box .name{color:var(--green);font-weight:600;display:flex;align-items:center;gap:5px}
.feed-box .name i{width:16px;height:16px;background:var(--green);display:inline-block}
.feed-box .faces{display:flex;gap:3px;margin-top:8px}
.feed-box .faces span{width:25px;height:25px;background:#9aa39a}
.signup{position:absolute;left:757px;top:2405px;width:316px;height:325px;background:var(--green-deep);padding:22px 28px;clip-path:polygon(26px 0,100% 0,100% 100%,0 100%,0 26px)}
.signup p{color:#dfe9df;font-size:11.5px;line-height:18px;margin-top:18px}
.signup .field{height:26px;background:var(--white);margin-top:10px;font-size:10px;color:#777;padding:6px 8px}
.signup .actions{display:flex;gap:14px;margin-top:14px}
.signup .actions span{height:28px;padding:0 14px;display:flex;align-items:center;font-family:"Oswald",sans-serif;font-size:13px;text-transform:uppercase}
.subscribe{background:var(--gold);color:#1d3a10}
.unsub{background:var(--green-dark);color:var(--white)}
.bottom{position:absolute;top:2730px;left:162px;width:876px;height:39px;display:flex;justify-content:space-between;align-items:center}
.bottom small{font-size:9px;color:#9ab79a}
.social{display:flex;gap:6px}
.social i{width:16px;height:16px;border-radius:50%;display:block;background:var(--green)}
</style>
</head>
<body>

<header class="site-header">
  <div class="brand"><span class="dot"></span>Ferndale Crest College</div>
  <div class="info">
    <svg width="18" height="22" viewBox="0 0 18 22"><rect x="3" y="1" width="12" height="20" rx="2" fill="none" stroke="#fff" stroke-width="2"/><rect x="7" y="16" width="4" height="2" fill="#fff"/></svg>
    <div><div class="label">INFORMATION CALL</div><div class="phone">0771 408 226</div></div>
  </div>
  <div class="search">SEARCH NOW!
    <div class="box">Enter Your Keyword...
      <svg width="12" height="12" viewBox="0 0 12 12"><circle cx="5" cy="5" r="3.8" fill="none" stroke="#666" stroke-width="1.5"/><line x1="8" y1="8" x2="11" y2="11" stroke="#666" stroke-width="1.5"/></svg>
    </div>
  </div>
  <nav class="nav">
    <span class="active">Home</span><span>About</span><span>Academics</span><span>Sports</span><span>Joining Ferndale Crest</span><span>Working at the College</span><span>Contact</span>
  </nav>
</header>

<section class="mosaic">
  <div role="img" aria-label="Rider on horseback jumping a fence" style="background:linear-gradient(#6f8f63,#3e5f34)"></div>
  <div role="img" aria-label="Students playing netball" style="background:linear-gradient(#a67a63,#7b5443)"></div>
  <div role="img" aria-label="Girls on the sports court" style="background:linear-gradient(#9a8f74,#6a5e46)"></div>
  <div role="img" aria-label="Goal posts on a field" style="background:linear-gradient(#9aa07a,#6b7a4a)"></div>
  <div role="img" aria-label="Students at an event" style="background:linear-gradient(#5f6e49,#3f4d2c)"></div>
  <div role="img" aria-label="Runner at the finish line" style="background:linear-gradient(#8a3f3a,#5a5d3a)"></div>
  <div role="img" aria-label="Student holding a school blazer" style="background:linear-gradient(#b9b2a2,#2f5f36)"></div>
  <div role="img" aria-label="Campus lawn with trees" style="background:linear-gradient(#4e7a3a,#3a5b2a)"></div>
  <div role="img" aria-label="Pupils in green uniforms" style="background:linear-gradient(#5a8052,#3b5a38)"></div>
  <div role="img" aria-label="Students on the lawn" style="background:linear-gradient(#6e8c5c,#4d6b3c)"></div>
  <div role="img" aria-label="Group of pupils together" style="background:linear-gradient(#6c5a48,#3b3a2f)"></div>
  <div role="img" aria-label="Sports field under blue sky" style="background:linear-gradient(#8aa0b8 30%,#4f7a3a 55%)"></div>
  <div role="img" aria-label="Student in a workshop" style="background:linear-gradient(#8a8778,#5a5a50)"></div>
  <div role="img" aria-label="Student in a science lab" style="background:linear-gradient(#c8c8c2,#7a8aa0)"></div>
</section>

<section class="wrap welcome">
  <h2 class="section-title">Welcome to <span>Ferndale Crest College</span></h2>
  <div class="text">
    <p>Welcome to Ferndale Crest Group of Schools where our School Motto is 'Tabelana' meaning Togetherness. We aim to work together in every aspect of School life, from academics to sport. Ferndale Crest College opened on 16th February 1949 and occupies 120 ha of land amidst the low hills of the Kestrel Range, 8km west of Marlow. This location encourages focus on School life away from the distractions and hustle and bustle of the larger towns.</p>
    <p>The day scholars have the option of selected bus drop off points for parents to collect day scholars closer to home. Ferndale Crest College offers a wide range of academic subjects alongside a varied sport and extra-curricular program.</p>
  </div>
  <div class="video" role="img" aria-label="Video still of the college main building and path">
    <svg class="play" width="50" height="50" viewBox="0 0 50 50"><circle cx="25" cy="25" r="22" fill="rgba(0,0,0,.35)" stroke="#fff" stroke-width="3"/><path d="M20 15 L35 25 L20 35Z" fill="#fff"/></svg>
  </div>
</section>

<div class="rule" style="top:946px"></div>

<section class="note" style="left:162px">
  <h2 class="section-title">Headmaster's <span>Welcome Note</span></h2>
  <div class="row">
    <div class="photo" role="img" aria-label="Portrait of the headmaster" style="background:linear-gradient(#5f7c57,#8a7a6a)"></div>
    <div>
      <p>Welcome to Ferndale Crest College. Here at the College we aim to encourage each pupil to be a self-confident, well rounded individual. We aim to propel them to the highest level of achievement in both academics and extra-curricular activities to provide them with the life skills they will need when they leave the College and to prepare them to be of value to society.</p>
      <span class="btn-more">Read More</span>
    </div>
  </div>
</section>
<section class="note" style="left:618px">
  <h2 class="section-title">Memorial Garden <span>Opened Speech Day 2011</span></h2>
  <div class="row">
    <div class="photo" role="img" aria-label="Students beside the memorial garden plaque" style="background:linear-gradient(#4f6a3c,#6a5a48)"></div>
    <div>
      <p>Every year the Lower Sixes choose a fundraising project - something for the community like a local orphanage or a local retirement home and then also do something to uplift the school. To uplift the school, the Lower Six Class of 2010 decided that they would like to honour and remember people who played a part in the development of the school.</p>
      <span class="btn-more">Read More</span>
    </div>
  </div>
</section>

<div class="rule" style="top:1304px"></div>

<section class="wrap calendar">
  <h2 class="section-title">School <span>Calender</span></h2>
  <table class="cal-table">
    <tr><th></th><th>First Term</th><th>Second Term</th><th>Third Term</th></tr>
    <tr class="band"><td class="label">Begins</td><td>Tuesday 14th January</td><td>Tuesday 13th May</td><td>Tuesday 9th September</td></tr>
    <tr><td class="label">1st Fixture Free</td><td>Friday 31st January –<br>Monday 3rd February</td><td>Friday 30th May –<br>Monday 2nd June</td><td>Friday 26th September –<br>Monday 29th September</td></tr>
    <tr class="band"><td class="label">Half-Term</td><td>Thursday 20th February –<br>Tuesday 25th February</td><td>Thursday 26th June –<br>Tuesday 1st July</td><td>Thursday 16th October –<br>Tuesday 21st October</td></tr>
    <tr><td class="label">2nd Fixture Free</td><td>Friday 14th March –<br>Monday 17th March</td><td>Friday 18th July –<br>Monday 21st July</td><td>Friday 7th November –<br>Monday 10th November</td></tr>
    <tr class="band"><td class="label">Term Ends</td><td>Thursday 10th April</td><td>Friday 7th August</td><td>Thursday 4th December</td></tr>
  </table>
</section>

<div class="downloads">
  <span class="btn-gold">Download Registration Form</span>
  <span class="btn-gold">2nd Term 2014 Termly Calendar</span>
</div>

<section class="wrap events">
  <h2 class="section-title">Upcoming <span>Events</span></h2>
  <div class="event" style="left:0">
    <div class="photo" role="img" aria-label="Basketball players on an outdoor court" style="background:linear-gradient(#a07a66,#7c5a4a)"></div>
    <div class="date">Fri 25 July 2014</div><div class="cap">Basketball CISA Top Schools</div>
  </div>
  <div class="event" style="left:223px">
    <div class="photo" role="img" aria-label="Pupils performing on a field" style="background:linear-gradient(#5a7a48,#8a7a5a)"></div>
    <div class="date">Sat 02 Aug 2013</div><div class="cap">School Play - Public Performance</div>
  </div>
  <div class="event" style="left:447px">
    <div class="photo" role="img" aria-label="Students gathered outdoors" style="background:linear-gradient(#6a7a4a,#4a5a38)"></div>
    <div class="date">Thurs 07 Aug 2013</div><div class="cap">Consultation for 4L, 5B, L6, U6</div>
  </div>
  <div class="sports">
    <h2 class="section-title">Sports <span>Announcements</span></h2>
    <ul><li>- Rugby</li><li>- Hockey Boys</li><li>- Soccer</li><li>- Hockey Girls</li><li>- Basketball Girls</li></ul>
  </div>
</section>

<div class="rule" style="top:2211px"></div>

<div class="partners">
  <div class="partner"><span></span></div>
  <div class="partner"><span></span></div>
  <div class="partner"><span></span></div>
  <div class="partner"><span></span></div>
</div>

<footer class="site-footer">
  <div class="touch">
    <h3 class="footer-title">Get in <span>Touch</span></h3>
    <div class="grid">
      <div class="item"><div class="ico"><svg width="14" height="16" viewBox="0 0 14 16"><path d="M7 1a5 5 0 0 1 5 5c0 4-5 9-5 9S2 10 2 6a5 5 0 0 1 5-5z" fill="#0b5a2a"/></svg></div><b>Ferndale Crest College</b>Lorem ipsum amet- 256894</div>
      <div class="item"><div class="ico"><svg width="14" height="16" viewBox="0 0 14 16"><path d="M7 1a5 5 0 0 1 5 5c0 4-5 9-5 9S2 10 2 6a5 5 0 0 1 5-5z" fill="#0b5a2a"/></svg></div><b>Map</b>Click here to see directions</div>
      <div class="item"><div class="ico"><svg width="14" height="16" viewBox="0 0 14 16"><rect x="3" y="1" width="8" height="14" rx="1.5" fill="#0b5a2a"/></svg></div><b>Phone Number</b>0771903145 / 0771408226</div>
      <div class="item"><div class="ico"><svg width="16" height="12" viewBox="0 0 16 12"><rect x="1" y="1" width="14" height="10" fill="#0b5a2a"/><path d="M1 1l7 6 7-6" fill="none" stroke="#f5e11a" stroke-width="1.2"/></svg></div><b>Email Us</b>admin@ferndalecrest.com</div>
    </div>
  </div>
  <div class="feed">
    <h3 class="footer-title">Social <span>Feeds</span></h3>
    <div class="feed-box">
      <div class="name"><i></i>Ferndale Crest School</div>
      <div style="margin-top:8px">1,176 people follow Ferndale Crest School</div>
      <div class="faces"><span></span><span></span><span></span><span></span><span></span><span></span></div>
      <div style="margin-top:10px;color:#999">Community feed</div>
    </div>
  </div>
</footer>

<aside class="signup">
  <h3 class="footer-title">Signup <span>Newsletter</span></h3>
  <p>If you would like to be added to the list of parents that receive the School Newsletter, please enter your details below.</p>
  <div class="field">Enter Your Name</div>
  <div class="field">Enter Your Email</div>
  <div class="actions"><span class="subscribe">Subscribe</span><span class="unsub">Unsubscribe</span></div>
</aside>

<div class="bottom">
  <small>© 2014 Ferndale Crest College. All rights reserved.</small>
  <div class="social"><i></i><i></i><i></i></div>
</div>

</body>
</html>
```